Business Card Re-Design/Update

We'd like to update out business cards. I've included our current "Style guide" which has the colour scheme of the organisation in it. I've also included the branding files with logos etc in them.

I've also included a copy of one of our existing cards so that you can see how ugly/dated they look. I'd like a fresh modern corporate look.

Target Market(s)

These are for our clients, potential clients, industry contacts - like all business cards

Contact Information for Business Card

Name
Position
Company Address - Level 1, 47 Fernby Street, Carlow Qld 4072
Direct Phone
mobile
Email
Website -www.korvalit.com.au
Logo

Colors

Designer to choose colors to be used in the design.

Requirements
Must have
• Main Logo
• Cards will need to be editable to be able to personalize them for each new employee.
Nice to have
• The MapOut, ShipWell, KeepSteady would be okay to have if they can be sensibly and professionally added to the look without detracting from the main imagery.
• Maybe they could go on the back of the card? will leave this to your creative discretion as to whether/where they fit.
Should not have
• Should not have decorative or script fonts

```html
<!DOCTYPE html>
<html lang="en">
<head>
<meta charset="utf-8">
<title>KorvalIT Business Card</title>
<link href="https://fonts.googleapis.com/css2?family=Roboto:wght@400;500;700&display=swap" rel="stylesheet">
<style>
  :root {
    --backdrop: #2b2b2d;
    --card-dark: #303133;
    --card-edge: #1c1c1e;
    --brand-blue: #1f86d1;
    --paper: #ffffff;
    --text-light: #e6e7e9;
    --text-muted: #b9bbbf;
  }
  * { box-sizing: border-box; margin: 0; padding: 0; }
  html, body { width: 1200px; height: 900px; overflow: hidden; }
  body {
    background: radial-gradient(ellipse at 55% 45%, #3a3a3c 0%, var(--backdrop) 55%, #1e1e20 100%);
    font-family: "Roboto", Arial, sans-serif;
    position: relative;
  }
  .card {
    position: absolute;
    border-radius: 26px;
    background: var(--card-dark);
    box-shadow: 0 6px 0 var(--card-edge), 0 12px 0 #262628, 0 24px 40px rgba(0,0,0,.55);
    overflow: hidden;
  }
  .card-front { left: 150px; top: 150px; width: 360px; height: 600px; }
  .card-back { left: 600px; top: 270px; width: 500px; height: 300px; display: flex; align-items: center; justify-content: center; }

  .brand-band {
    height: 190px;
    background: var(--paper);
    display: flex;
    align-items: center;
    justify-content: center;
    gap: 14px;
  }
  .brand-mark { width: 26px; height: 26px; background: var(--brand-blue); border-radius: 3px; }
  .brand-name { font-size: 44px; font-weight: 500; color: var(--brand-blue); letter-spacing: .5px; }

  .details { padding: 44px 36px 0; }
  .person-name { font-size: 26px; font-weight: 500; color: var(--brand-blue); text-transform: uppercase; letter-spacing: .5px; }
  .person-role { font-size: 14px; color: var(--text-muted); margin-top: 4px; }
  .address { font-size: 15px; color: var(--text-light); line-height: 1.45; margin-top: 26px; }
  .contact-list { list-style: none; margin-top: 24px; }
  .contact-list li { display: flex; align-items: center; gap: 12px; font-size: 15px; color: var(--text-light); line-height: 1.75; }
  .contact-list svg { width: 13px; height: 13px; flex: none; fill: var(--brand-blue); }
  .web-accent { color: var(--brand-blue); }

  .sub-brand { font-size: 64px; font-weight: 500; color: var(--brand-blue); letter-spacing: .5px; }
  .sub-mark { width: 36px; height: 36px; background: var(--brand-blue); border-radius: 4px; margin-right: 18px; }
</style>
</head>
<body>
  <section class="card card-front">
    <header class="brand-band">
      <span class="brand-mark"></span>
      <span class="brand-name">korvalIT</span>
    </header>
    <div class="details">
      <h1 class="person-name">Maren Holt</h1>
      <p class="person-role">Business Development Manager</p>
      <p class="address">12/58 Ardley Road,<br>Paxton QLD 4011</p>
      <ul class="contact-list">
        <li><svg viewBox="0 0 16 16"><rect x="4" y="1" width="8" height="14" rx="1.5"/></svg><span>+61 (0)400 555 182</span></li>
        <li><svg viewBox="0 0 16 16"><path d="M3 2h3l1.5 4-2 1.2a9 9 0 0 0 3.3 3.3L10 8.5l4 1.5v3a1 1 0 0 1-1 1A12 12 0 0 1 2 3a1 1 0 0 1 1-1z"/></svg><span>+61 (0)7 5550 1316</span></li>
        <li><svg viewBox="0 0 16 16"><path d="M3 2h3l1.5 4-2 1.2a9 9 0 0 0 3.3 3.3L10 8.5l4 1.5v3a1 1 0 0 1-1 1A12 12 0 0 1 2 3a1 1 0 0 1 1-1z"/></svg><span>+61 (0)7 5550 1333</span></li>
        <li><svg viewBox="0 0 16 16"><rect x="2" y="5" width="12" height="8" rx="1"/><rect x="4" y="2" width="8" height="4"/></svg><span>+61 (0)7 5550 1303</span></li>
        <li><svg viewBox="0 0 16 16"><path d="M1 3h14v10H1zM2 4l6 5 6-5"/></svg><span>mholt@korvalit.com.au</span></li>
        <li><svg viewBox="0 0 16 16"><circle cx="8" cy="8" r="7"/></svg><span>www.<span class="web-accent">korvalit</span>.com.au</span></li>
      </ul>
    </div>
  </section>

  <section class="card card-back">
    <span class="sub-mark"></span>
    <span class="sub-brand">Parcevon</span>
  </section>
</body>
</html>
```